Brevard Trade Partners - we are Asian sourcing agents

We are sourcing agents based in the USA and we act as sourcing agents for clients in throughout the world. We focus primarily on custom sewn goods. So basically companies who do not have the in-house expertise to do it themselves, come to us and have us find suitable factories in Asia to do the production. We are middlemen. We find the factories...quote the project...manage the quality control and then deliver the goods directly to our customer's door. We pride ourselves in making the communication very easy and precise.

Current page is www.brevardtradepartners.com

I am not happy w/ the overall look. The spacing...the photos, the fonts...the design elements...the pictures. I want a cool, crisp design that conveys professionalism and clearly depicts/explains what we do.

Requirements
Must have
• use my logo....I like it...it was designed by someone on this website.
Nice to have
• a video/animation of the entire process would be wonderful. Showing initial contact with our office in the USA...then to my correspondence with my offices in Taiwan and in Hong Kong...and then back and fort w/ the customer.....and then between my people in Hong Kong/Taiwan with the local factories......and then a quote is generated and sent to my client......to samples being made and sent for approval.....to a PO being generated......to final samples being sent.....to the order being shipped and delivered to the clients warehouse. I was thinking of an animation showing arrows and text showing the back and forth communication and explaining how the process flows.

```html
<!DOCTYPE html>
<html lang="en">
<head>
<meta charset="utf-8">
<title>Brevard Trade Partners – Asian Outsourcing Made Easy</title>
<link rel="stylesheet" href="https://fonts.googleapis.com/css2?family=Ubuntu:wght@400;500;700&family=Open+Sans:wght@400;600;700&display=swap">
<style>
:root{
  --navy:#1e2b63;
  --green:#7a9a1e;
  --green-light:#9fc131;
  --orange:#f26a1b;
  --orange-dark:#d9520b;
  --text:#444;
  --white:#fff;
  --footer:#1b1b1b;
  --footer-line:#3a3a3a;
  --footer-text:#b3b3b3;
  --bottom:#0e0e0e;
}
*{margin:0;padding:0;box-sizing:border-box}
html,body{width:1200px;height:2687px;overflow:hidden}
body{position:relative;background:var(--white);font-family:"Open Sans",Arial,sans-serif;color:var(--text)}
.abs{position:absolute}
ul{list-style:none}

/* header */
.site-header{position:absolute;left:0;top:0;width:1200px;height:120px;background:var(--white)}
.brand{position:absolute;left:111px;top:36px;font-family:"Ubuntu",sans-serif;font-weight:700;color:var(--navy);font-size:29px;line-height:30px;letter-spacing:.5px}
.brand small{display:block;font-size:19px;line-height:24px;letter-spacing:1.4px}
.contact-bar{position:absolute;right:110px;top:26px;display:flex;gap:36px;font-size:15px;color:#555;white-space:nowrap}
.contact-bar span{display:flex;align-items:center;gap:10px}
.main-nav{position:absolute;right:110px;top:67px;display:flex;gap:20px;font-size:15px;font-weight:600;color:#333;text-transform:uppercase;white-space:nowrap}
.main-nav a{padding:6px 10px;color:inherit;text-decoration:none}
.main-nav a.active{background:var(--green);color:var(--white)}

/* hero */
.hero{position:absolute;left:0;top:120px;width:1200px;height:501px;background:linear-gradient(100deg,#3a2a20 0%,#6a4a35 40%,#8a6a55 60%,#5a4a45 100%)}
.hero h1{position:absolute;left:111px;top:125px;font-family:"Ubuntu",sans-serif;font-weight:400;font-size:53px;line-height:55px;color:var(--green-light)}
.hero p{position:absolute;left:111px;top:248px;font-family:"Ubuntu",sans-serif;font-size:29px;line-height:31px;color:var(--white)}
.btn-quote{position:absolute;display:flex;align-items:center;justify-content:space-between;padding:0 10px 0 22px;height:44px;width:256px;background:linear-gradient(var(--orange),var(--orange-dark));color:var(--white);font-family:"Ubuntu",sans-serif;font-size:22px;line-height:44px;white-space:nowrap;border-radius:3px}
.btn-quote svg{flex:none}
.hero .btn-quote{left:111px;top:333px}

/* services */
.section-title{position:absolute;width:1200px;text-align:center;font-family:"Ubuntu",sans-serif;font-weight:400;color:#222}
.services-title{top:670px;font-size:36px}
.service{position:absolute;top:750px;width:230px;text-align:center}
.service .ring{width:172px;height:172px;margin:0 auto;border:5px solid var(--green);border-radius:50%;background:#f4f4f4;display:flex;align-items:center;justify-content:center}
.service .thumb{width:110px;height:80px;border-radius:8px}
.service h3{margin-top:17px;font-family:"Ubuntu",sans-serif;font-weight:500;font-size:26px;color:#222}
.service p{margin-top:6px;font-size:14.5px;line-height:20px;color:#444}
.btn-small{display:inline-block;width:80px;height:25px;line-height:25px;background:var(--navy);color:var(--white);font-size:12px;font-weight:600;border-radius:2px;text-align:center;white-space:nowrap}
.service .btn-small{margin-top:15px}
.slider-arrow{position:absolute;top:885px}

/* band */
.china-band{position:absolute;left:0;top:1137px;width:1200px;height:350px;background:linear-gradient(180deg,#3c4a3a 0%,#2c3a28 50%,#1e2a1a 100%)}
.china-band h2{position:absolute;top:56px;width:1200px;text-align:center;font-family:"Ubuntu",sans-serif;font-weight:500;font-size:37px;color:var(--white)}
.china-band p{position:absolute;left:150px;top:122px;width:900px;text-align:center;font-size:18.5px;line-height:30px;color:#eee}
.btn-green{display:inline-block;background:var(--green);color:var(--white);font-weight:600;text-align:center;border-radius:2px;white-space:nowrap}
.china-band .btn-green{position:absolute;left:548px;top:262px;width:104px;height:36px;line-height:36px;font-size:15px}

/* about + video */
.col-heading{position:absolute;top:1540px;font-family:"Ubuntu",sans-serif;font-weight:400;font-size:31px;color:#222;padding-bottom:6px;border-bottom:3px solid #ccc;white-space:nowrap}
.col-heading::after{content:"";position:absolute;left:0;bottom:-3px;width:115px;height:3px;background:var(--green)}
.about-text{position:absolute;left:115px;top:1593px;width:480px;font-size:17px;line-height:25px;color:#444}
.about-text p+p{margin-top:25px}
.about-btn{position:absolute;left:111px;top:1824px;width:104px;height:36px;line-height:36px;font-size:15px}
.video{position:absolute;left:647px;top:1599px;width:441px;height:270px;background:#222;box-shadow:0 2px 6px rgba(0,0,0,.4)}
.video-still{position:absolute;left:4px;top:4px;width:433px;height:228px;background:linear-gradient(120deg,#5f6b78,#9aa3ad 45%,#7c7a78 70%,#4a4e55)}
.video-controls{position:absolute;left:0;bottom:0;width:441px;height:38px;background:linear-gradient(#3a3a3a,#151515)}

/* cta */
.cta-band{position:absolute;left:0;top:1917px;width:1200px;height:121px;background:linear-gradient(90deg,#3a2616 0%,#6b4420 50%,#3e2a18 100%);border-bottom:6px solid var(--green)}
.cta-band h2{position:absolute;left:111px;top:33px;font-family:"Ubuntu",sans-serif;font-weight:400;font-size:25px;color:var(--white);white-space:nowrap}
.cta-band p{position:absolute;left:111px;top:66px;font-size:14px;color:#eee;white-space:nowrap}
.cta-band .btn-quote{left:834px;top:40px}

/* footer */
.site-footer{position:absolute;left:0;top:2044px;width:1200px;height:592px;background:var(--footer)}
.f-col{position:absolute}
.f-col h4{font-family:"Ubuntu",sans-serif;font-weight:500;font-size:22px;line-height:26px;color:var(--white);margin-bottom:14px}
.f-col ul{width:195px}
.f-col.hq ul{width:250px}
.f-col li{font-size:13.5px;line-height:27px;color:var(--footer-text);border-bottom:1px solid var(--footer-line);padding-left:17px;position:relative;white-space:nowrap}
.f-col li::before{content:"›";position:absolute;left:2px;top:-1px;color:#888}
.f-col .gap{margin-top:30px}
.f-sub{font-size:13.5px;font-weight:700;color:var(--white);margin:14px 0 10px}
.follow{position:absolute;left:111px;top:382px;display:flex;align-items:center;gap:6px;font-size:14px;color:var(--white)}
.follow i{display:block;width:26px;height:26px;border:2px solid var(--white);border-radius:50%}
.footer-brand{position:absolute;left:111px;top:432px;font-family:"Ubuntu",sans-serif;font-weight:700;color:#7c7c7c;font-size:34px;line-height:32px}
.footer-brand small{display:block;font-size:17px;line-height:22px;letter-spacing:1px}
.bottom-bar{position:absolute;left:0;top:2636px;width:1200px;height:51px;background:var(--bottom);font-size:13px;color:#ddd;white-space:nowrap}
.bottom-bar .copy{position:absolute;left:111px;top:16px}
.bottom-bar .legal{position:absolute;right:110px;top:16px}
</style>
</head>
<body>

<header class="site-header">
  <div class="brand">Brevard Trade<small>PARTNERS</small></div>
  <div class="contact-bar">
    <span><svg width="18" height="18" viewBox="0 0 24 24"><path d="M6.6 10.8a15 15 0 0 0 6.6 6.6l2.2-2.2c.3-.3.7-.4 1-.2 1.1.4 2.3.6 3.6.6.6 0 1 .4 1 1V20c0 .6-.4 1-1 1A17 17 0 0 1 3 4c0-.6.4-1 1-1h3.5c.6 0 1 .4 1 1 0 1.3.2 2.5.6 3.6.1.3 0 .7-.2 1z" fill="#7a9a1e"/></svg>+1 321 555 0148</span>
    <span><svg width="20" height="14" viewBox="0 0 20 14"><rect x="0.5" y="0.5" width="19" height="13" fill="#7a9a1e"/><path d="M1 1l9 7 9-7" stroke="#fff" fill="none" stroke-width="1.5"/></svg>info@brevardtradepartners.com</span>
  </div>
  <nav class="main-nav">
    <a class="active">Home</a><a>Product Categories</a><a>About Us</a><a>Request Quote</a>
  </nav>
</header>

<section class="hero">
  <div class="abs" style="inset:0" role="img" aria-label="Close-up of a sewing machine stitching a leather piece"></div>
  <h1>Asian Outsourcing<br>Made Easy!</h1>
  <p>Custom Sewn Goods Made to<br>Your Specifications</p>
  <div class="btn-quote"><span>Get a Free Quote</span>
    <svg width="32" height="32" viewBox="0 0 32 32"><circle cx="16" cy="16" r="15" fill="#fff"/><path d="M11 10h6l6 6-6 6h-6l6-6z" fill="#f26a1b"/></svg>
  </div>
</section>

<h2 class="section-title services-title">OUR SEVICES</h2>
<svg class="slider-arrow" style="left:86px" width="24" height="56" viewBox="0 0 24 56"><path d="M22 2L2 28l20 26" stroke="#333" stroke-width="2" fill="none"/></svg>
<svg class="slider-arrow" style="left:1092px" width="24" height="56" viewBox="0 0 24 56"><path d="M2 2l20 26L2 54" stroke="#333" stroke-width="2" fill="none"/></svg>

<div class="service" style="left:114px">
  <div class="ring"><div class="thumb" role="img" aria-label="Messenger bag" style="background:linear-gradient(#444,#222 60%,#b22)"></div></div>
  <h3>BAGS</h3><p>Lorem ipsum dolor sit amet<br>con sectetur adip ipsum dolor<br>consecetur.</p><span class="btn-small">Read More</span>
</div>
<div class="service" style="left:358px">
  <div class="ring"><div class="thumb" role="img" aria-label="Pair of gloves" style="background:linear-gradient(90deg,#ddd,#555 50%,#ddd)"></div></div>
  <h3>GLOVES</h3><p>Lorem ipsum dolor sit amet<br>con sectetur adip ipsum dolor<br>consecetur.</p><span class="btn-small">Read More</span>
</div>
<div class="service" style="left:607px">
  <div class="ring"><div class="thumb" role="img" aria-label="Motorcycle cover" style="background:radial-gradient(ellipse at 50% 40%,#3a4fb0,#1c2a7a)"></div></div>
  <h3>COVERS</h3><p>Lorem ipsum dolor sit amet<br>con sectetur adip ipsum dolor<br>consecetur.</p><span class="btn-small">Read More</span>
</div>
<div class="service" style="left:861px">
  <div class="ring"><div class="thumb" role="img" aria-label="Colourful phone cases" style="background:linear-gradient(90deg,#c33,#a3c,#36c,#c3a,#888)"></div></div>
  <h3>CASES</h3><p>Lorem ipsum dolor sit amet<br>con sectetur adip ipsum dolor<br>consecetur.</p><span class="btn-small">Read More</span>
</div>

<section class="china-band">
  <div class="abs" style="inset:0" role="img" aria-label="Great Wall of China winding over green hills"></div>
  <h2>Sourcing Custom Goods In China</h2>
  <p>We outsource sewing services direct from China. Our long-established and extensive network of offshore factory-partners provides our clients with access to a wide variety of contract sewing expertise from Chinese manufacturers.Clients only need to communicate with our US agents,but will have thebenefits of the cost savings &amp; quality workmanship from offshore outsourcing from Asia.</p>
  <span class="btn-green">Read More</span>
</section>

<h2 class="col-heading" style="left:111px;width:485px">Sourcing Custom Goods In China</h2>
<div class="about-text">
  <p>We outsource sewing services direct from China. Our long-established and extensive network of offshore factory-partners provides our clients with access to a wide variety of contract sewing expertise from Chinese manufacturers.</p>
  <p>Clients only need to communicate with our US agents,but will have the benefits of the cost savings &amp; quality workmanship from offshore outsourcing from Asia.</p>
</div>
<span class="btn-green about-btn">Read More</span>

<h2 class="col-heading" style="left:645px;width:444px">Watch Our Video</h2>
<div class="video">
  <div class="video-still" role="img" aria-label="Worker operating a sewing machine in a factory"></div>
  <svg class="abs" style="left:194px;top:88px" width="54" height="54" viewBox="0 0 54 54"><circle cx="27" cy="27" r="26" fill="rgba(255,255,255,.35)"/><path d="M20 14l20 13-20 13z" fill="#fff"/></svg>
  <div class="video-controls">
    <svg width="441" height="38" viewBox="0 0 441 38">
      <rect x="22" y="12" width="240" height="4" fill="#555"/><rect x="22" y="12" width="120" height="4" fill="#d22"/>
      <text x="248" y="30" font-size="11" fill="#ddd" font-family="Open Sans,sans-serif">1:26 / 3:22</text>
      <path d="M310 22l6-4v8z" fill="#ddd"/><rect x="322" y="20" width="26" height="3" fill="#d22"/>
      <rect x="380" y="17" width="11" height="8" fill="none" stroke="#ddd" stroke-width="1.5"/>
      <text x="402" y="26" font-size="12" font-weight="700" font-style="italic" fill="#ddd" font-family="Open Sans,sans-serif">HD</text>
    </svg>
  </div>
</div>

<section class="cta-band">
  <div class="abs" style="inset:0" role="img" aria-label="Sunset silhouette of Chinese rooftops"></div>
  <h2>Outsource Your Sewing Needs to Trusted Contractors in China</h2>
  <p>Please contact us for immediate consultation regarding your outsourcing project.</p>
  <div class="btn-quote"><span>Get a Free Quote</span>
    <svg width="32" height="32" viewBox="0 0 32 32"><circle cx="16" cy="16" r="15" fill="#fff"/><path d="M11 10h6l6 6-6 6h-6l6-6z" fill="#f26a1b"/></svg>
  </div>
</section>

<footer class="site-footer">
  <div class="f-col hq" style="left:111px;top:44px">
    <h4>Us Headquarters</h4>
    <ul><li>Brevard Trade Partners, LLC</li><li>Forty Harbor Street</li><li>Suite B-4</li><li>Melbourne, FL 32901</li></ul>
    <div class="f-sub">Online: Inquiry Form</div>
    <ul><li>Tel: 321-555-0162</li><li>Fax: 321-555-0177</li><li>Mail: team@brevardtradepartners.com</li></ul>
  </div>
  <div class="follow">Follow Us: <i></i><i></i><i></i></div>
  <div class="footer-brand">Brevard Trade<small>PARTNERS</small></div>

  <div class="f-col" style="left:403px;top:44px">
    <h4>Custom Bags</h4>
    <ul><li>Athletic Bags</li><li>Backpacks</li><li>Computer Bags</li><li>Cooler Bags</li><li>Cosmetic Bags</li><li>Handbags</li><li>Messenger Bags</li><li>Shopping Bags</li><li>Tool Bags</li><li>Travel Bags</li><li>Yoga Bags</li></ul>
    <h4 class="gap">Custom Sporting<br>Goods</h4>
    <ul><li>Yoga Mats</li><li>Yoga Gear and Accessories</li></ul>
  </div>

  <div class="f-col" style="left:638px;top:44px">
    <h4>Custom Covers</h4>
    <ul><li>ATV Covers</li><li>Chair Covers</li><li>Equipment Covers</li><li>Golf Cart Covers</li><li>Motorcycle Covers</li><li>Outdoor Furniture Covers</li><li>Outdoor Grill Cover</li><li>Personal Watercraft Covers</li><li>Snowmobile Covers</li></ul>
    <h4 class="gap">Custom Medical<br>Accessories</h4>
    <ul style="width:210px"><li>Medical Equipment Covers</li><li>Medical Pads</li><li>Medical Sheets &amp; Bedding</li><li>Oxygen Tank Cases and Bags</li></ul>
  </div>

  <div class="f-col" style="left:896px;top:44px">
    <h4>Custom Gloves</h4>
    <ul><li>Batting Gloves</li><li>Garden Gloves</li><li>Mechanic Gloves</li><li>Safety Gloves</li><li>Ski Gloves</li></ul>
    <h4 class="gap">Custom Sewn<br>Goods</h4>
    <ul><li>Pet Collars, Leashes</li><li>Socks</li></ul>
    <h4 class="gap">Custom Cases</h4>
    <ul><li>Cosmetic Cases</li><li>Phone Cases</li><li>Tool Bags and Tool</li><li>Cases</li></ul>
  </div>
</footer>

<div class="bottom-bar">
  <span class="copy">Copyrights © 2015. Brevard Trade Partners . All Rights Reserved</span>
  <span class="legal">Privacy Policy &nbsp; | &nbsp; Terms &amp; Condition</span>
</div>

</body>
</html>
```